Homeowners Insurance Provider Website

We are selling homeowners insurance policy / tenants Policy/Flood Insurance in USA in few states and planning expand nationally.

Our target audience are two folds: Customers (Buy policies) and Insurance Agents who wants to work with us to sell our policies to customers. But website should focus 80% on customers and 20% on agents. So, more customer focused user experience. Please note that there is no direct buy option for customers. They always go through insurance agents.

Customer focused, educational that makes buyer journey easy. We don’t want to come off as trying sell something as there is no direct sales involved from website.

Target Market(s)

Homeowners in USA and Insurance agent who sells these insurance.

Industry/Entity Type

Insurance

Number of Pages Required

4 page

Font styles to use
Other font styles liked:
• Open to suggestions

Colors

Designer to choose colors to be used in the design.

Requirements
Must have
• Three most important things: Trustworthy, Authentic, Simple
• Please use colors form logo and grays
• We like: www.hollowmere.com
• https://www.quillfenbrook.com/
• We need Agent Look up tool on home page similar to what is shown on example sites.
• Design:
• Home Page - Open to Ideas
• Insurance (Products) Landing Page - Info similar to: https://www.quillfenbrook.com/insurance/
• Agents Page - https://www.quillfenbrook.com/agents/
• Claims Page - Information similar to: https://www.quillfenbrook.com/claims-center/
• Site Navigation:
• Home
• Insurance
• Claims
• Agents
• About Us
• Contact Us
Nice to have
• Elegant, minimal and clean design that reflects trust and authenticity.
Should not have
• Slider or rotating images - prefer flat design. Not over powering design.

```html
<!DOCTYPE html>
<html lang="en">
<head>
<meta charset="utf-8">
<title>Hearthline Insurance Co.</title>
<link href="https://fonts.googleapis.com/css2?family=Open+Sans:wght@400;600;700&family=Raleway:wght@400;500;600&display=swap" rel="stylesheet">
<style>
:root{
  --red:#e02228;
  --red-dark:#c91d24;
  --navy:#213a7a;
  --navy-deep:#172a57;
  --ink:#222;
  --gray:#555;
  --line:#d6d6d6;
  --field:#f1f1f1;
  --paper:#fff;
  --soft:#f4f4f4;
  --footer:#1f1f1f;
  --footer-bar:#1a2f66;
}
*{box-sizing:border-box;margin:0;padding:0}
html,body{width:1200px;height:2903px;overflow:hidden}
body{font-family:"Raleway",Arial,sans-serif;color:var(--ink);background:var(--paper);position:relative}
.wrap{position:absolute;left:141px;width:918px}
.btn{display:inline-block;font-family:"Open Sans",Arial,sans-serif;font-size:13px;font-weight:600;text-transform:uppercase;color:#fff;padding:0 22px;line-height:28px;letter-spacing:.3px}
.btn-red{background:var(--red)}
.btn-navy{background:var(--navy)}
.btn-white{background:#fff;color:var(--red)}
p{font-size:13px;line-height:21px}

/* hero */
.hero{position:absolute;left:0;top:0;width:1200px;height:548px}
.hero-photo{position:absolute;inset:0;background:linear-gradient(180deg,#4b5a70 0%,#7f8fa3 45%,#5d6b7e 75%,#3d4a5c 100%)}
.hero-photo .umbrella{position:absolute;left:690px;top:40px;width:260px;height:110px;border-radius:130px 130px 10px 10px;background:#c8323a;opacity:.85}
.header{position:absolute;left:141px;top:35px;width:929px;height:85px;background:rgba(255,255,255,.9);display:flex;align-items:center;padding:0 14px}
.brand{display:flex;align-items:center;gap:12px}
.brand-mark{width:46px;height:46px;background:var(--navy)}
.brand-name{font-family:"Open Sans",Arial,sans-serif;font-weight:700;color:var(--navy);font-size:21px;line-height:22px;text-transform:uppercase}
.nav{margin-left:auto;display:flex;align-items:center;gap:20px;font-size:13px;font-weight:500;color:#333}
.nav .current{color:var(--red)}
.nav .quote{background:var(--navy);color:#fff;padding:0 10px;line-height:28px}
.hero-card{position:absolute;left:141px;top:271px;width:492px;height:141px;background:rgba(255,255,255,.88);border-radius:6px;padding:16px 18px}
.hero-card h1{font-family:"Open Sans",Arial,sans-serif;font-weight:600;font-size:25px;line-height:33px;color:var(--ink);text-transform:uppercase;letter-spacing:.5px}
.hero-card .btn{position:absolute;left:22px;top:126px}

/* products */
.products{position:absolute;top:464px;left:0;width:1200px}
.product{position:absolute;width:180px;text-align:center}
.product .ring{width:164px;height:164px;margin:0 auto;border-radius:50%;background:#fff;border:8px solid #eceef2;display:flex;align-items:center;justify-content:center}
.product .icon{width:50px;height:50px;border-radius:50%;background:var(--red)}
.product h3{margin-top:14px;font-family:"Open Sans",Arial,sans-serif;font-weight:600;font-size:15px;color:var(--red);line-height:21px;text-transform:uppercase}

/* about */
.about{top:730px;left:141px;position:absolute;width:618px}
.section-title{font-family:"Open Sans",Arial,sans-serif;font-size:25px;font-weight:600;color:var(--ink);letter-spacing:.5px;text-transform:uppercase}
.rule{height:1px;background:var(--line);position:relative;margin:14px 0 22px}
.rule::before{content:"";position:absolute;left:0;top:-2px;width:62px;height:4px;background:var(--navy)}
.about p{font-size:13px;line-height:24px;color:#333}
.about .btn{margin-top:18px}
.quote-form{position:absolute;left:818px;top:720px;width:240px;height:282px;background:#f2f2f2;border:1px solid #ddd}
.quote-form h2{background:var(--navy);color:#fff;font-family:"Open Sans",Arial,sans-serif;font-weight:600;font-size:20px;text-align:center;line-height:36px}
.quote-form form{padding:14px 14px}
.field{display:block;width:100%;height:30px;margin-bottom:8px;background:#e8e8e8;border:1px solid #d4d4d4;font-family:inherit;font-size:11px;color:#888;padding:0 10px;line-height:28px}
.field.tall{height:50px}
.quote-form .submit{display:block;width:100%;text-align:center;background:var(--navy);color:#fff;font-size:12px;font-weight:600;line-height:32px;margin-top:6px;font-family:"Open Sans",Arial,sans-serif}

/* audience band */
.audience{position:absolute;top:1058px;left:0;width:1200px;height:327px;display:flex}
.audience .half{width:600px;height:100%;color:#fff;position:relative}
.audience .customers{background:var(--red)}
.audience .agents{background:var(--navy)}
.audience h3{font-family:"Open Sans",Arial,sans-serif;font-size:18px;font-weight:600;position:absolute;top:52px}
.audience p{position:absolute;top:86px;width:330px;font-size:13px;line-height:21px}
.audience .btn{position:absolute;top:244px}
.customers h3,.customers p,.customers .btn{left:141px}
.agents h3,.agents p,.agents .btn{right:141px;text-align:right}
.emblem{position:absolute;left:525px;top:1108px;width:150px;height:150px;border-radius:50%;background:#fff;border:10px solid var(--navy)}

/* insurance */
.insurance{position:absolute;top:1385px;left:0;width:1200px;height:627px;background:var(--soft)}
.insurance .heading{position:absolute;top:48px;left:292px;width:616px;text-align:center}
.insurance .heading .rule{margin:14px 0 0}
.insurance .heading .rule::before{left:277px}
.cards{position:absolute;left:141px;top:157px;width:918px;height:414px;display:flex}
.card{width:306px;height:100%;position:relative;overflow:hidden;color:#fff;text-align:center}
.card .photo{position:absolute;inset:0}
.card.home .photo{background:linear-gradient(180deg,#e9e6e2 0%,#b7aca0 55%,#1b1b1b 100%)}
.card.tenant .photo{background:linear-gradient(180deg,#d9c1a5 0%,#9c8670 50%,#6c5b4c 100%)}
.card.flood .photo{background:linear-gradient(180deg,#6f8a4e 0%,#8c4b3b 55%,#1b1b1b 100%)}
.card .body{position:absolute;left:0;right:0;bottom:0;padding:0 24px 28px}
.card.tenant .body{background:rgba(33,58,122,.82);top:200px;padding-top:20px}
.card h4{font-family:"Open Sans",Arial,sans-serif;font-weight:600;font-size:20px}
.card .mini{width:70px;height:2px;background:var(--red);margin:10px auto 12px}
.card p{font-size:11.5px;line-height:18px}
.card .actions{display:flex;justify-content:center;gap:12px;margin-top:18px}
.card .actions .btn{font-size:12px;padding:0 16px;line-height:30px}

/* agent finder */
.finder{position:absolute;top:2012px;left:0;width:1200px;height:294px;background:var(--navy-deep);text-align:center;color:#fff}
.finder h2{font-family:"Open Sans",Arial,sans-serif;font-weight:600;font-size:25px;margin-top:50px;letter-spacing:.5px}
.finder .bar{width:62px;height:3px;background:#fff;margin:12px auto 18px}
.finder p{width:610px;margin:0 auto;font-size:13px;line-height:23px}
.finder .search{display:flex;justify-content:center;gap:8px;margin-top:22px}
.finder .search span{width:156px;height:30px;background:#fff;color:#999;font-size:11px;text-align:left;padding-left:10px;line-height:30px}
.finder .search .btn{width:156px;padding:0;line-height:30px}

/* claim + contact */
.claim{position:absolute;top:2358px;left:141px;width:300px;text-align:center}
.claim h3{font-family:"Open Sans",Arial,sans-serif;font-weight:600;font-size:27px;color:var(--navy-deep)}
.claim .big{font-family:"Open Sans",Arial,sans-serif;font-weight:700;font-size:54px;color:var(--red);line-height:62px}
.claim p{font-size:14px;color:var(--navy-deep);line-height:23px;margin-top:6px}
.claim .btn{margin-top:30px;padding:0 26px}
.divider{position:absolute;left:441px;top:2352px;width:1px;height:210px;background:var(--line)}
.contact{position:absolute;top:2352px;left:484px;width:528px}
.contact .rule{margin:12px 0 18px}
.contact .hint{font-size:11px;color:#444;margin-bottom:10px}
.contact .grid{display:grid;grid-template-columns:258px 258px;gap:14px 12px}
.contact .field{background:#fff;height:30px;margin:0}
.contact .btn{margin-top:18px;padding:0 16px}

/* footer */
.footer{position:absolute;top:2618px;left:0;width:1200px;height:250px;background:var(--footer);color:#ddd}
.footer h5{font-family:"Raleway",Arial,sans-serif;font-weight:500;font-size:16px;color:#fff;padding-bottom:8px;border-bottom:1px solid #444;margin-bottom:14px}
.fcol{position:absolute;top:42px}
.links{left:159px;width:100px}
.links li{list-style:none;font-size:11px;line-height:22px;color:#ccc}
.links li::before{content:"›";margin-right:6px;color:#888}
.links li.current{color:var(--navy)}
.details{left:339px;width:185px;font-size:11px}
.details .name{font-size:12px;color:#fff}
.details p{font-size:11px;line-height:17px;color:#aaa}
.details .row{display:flex;align-items:center;gap:10px;margin-top:18px;font-size:14px}
.details .row.mail{font-size:11px;margin-top:16px}
.news{left:623px;width:215px}
.news p{font-size:11px;line-height:17px;color:#aaa}
.news .email{margin-top:12px;width:173px;height:30px;background:#3a3a3a;color:#ddd;font-size:11px;line-height:30px;padding-left:10px}
.news .btn{margin-top:10px;font-size:12px;padding:0 16px;line-height:28px;text-transform:none}
.fbrand{position:absolute;left:905px;top:58px;width:150px;height:150px;display:flex;align-items:center;justify-content:center;flex-direction:column;gap:10px}
.fbrand .sq{width:70px;height:70px;border:4px solid #bbb}
.fbrand span{font-family:"Open Sans",Arial,sans-serif;font-size:13px;font-weight:600;color:#bbb;text-transform:uppercase}
.legal{position:absolute;top:2868px;left:0;width:1200px;height:35px;background:var(--footer-bar);color:#fff;font-size:11px;font-family:"Open Sans",Arial,sans-serif;font-weight:600}
.legal .copy{position:absolute;left:141px;top:10px}
.social{position:absolute;right:141px;top:8px;display:flex;gap:6px}
.social span{width:20px;height:20px;border:1px solid #fff;background:#2d4a95}
</style>
</head>
<body>

<section class="hero">
  <div class="hero-photo" role="img" aria-label="Businessman holding a red umbrella under a stormy sky over a city skyline"><div class="umbrella"></div></div>
  <header class="header">
    <div class="brand">
      <div class="brand-mark"></div>
      <div class="brand-name">Hearthline<br>Insurance Co.</div>
    </div>
    <nav class="nav">
      <span class="current">Home</span><span>About Us</span><span>Insurance</span><span>Agents</span><span>Claims</span><span>Contact Us</span><span class="quote">Get a quote</span>
    </nav>
  </header>
  <div class="hero-card">
    <h1>Get Homeowners Insurance Policy / Tenants Policy/ Flood Insurance in USA</h1>
    <span class="btn btn-red">Read More</span>
  </div>
</section>

<section class="products">
  <div class="product" style="left:220px"><div class="ring"><div class="icon" role="img" aria-label="House in hand icon"></div></div><h3>Homeowners<br>Policy</h3></div>
  <div class="product" style="left:508px"><div class="ring"><div class="icon" role="img" aria-label="Family in house icon"></div></div><h3 style="margin-top:24px">Tenants Policy</h3></div>
  <div class="product" style="left:790px"><div class="ring"><div class="icon" role="img" aria-label="House in flood water icon"></div></div><h3 style="margin-top:24px">Flood Insurance</h3></div>
</section>

<section class="about">
  <h2 class="section-title">About Us</h2>
  <div class="rule"></div>
  <p>Lorem ipsum dolor sit amet, consectetuer adipiscing elit, sed diam nonummy nibh euismod tincidunt ut laoreet dolore magna aliquam erat volutpat. Ut wisi enim ad minim veniam, quis nostrud exerci tation ullamcorper suscipit lobortis nisl ut aliquip ex ea commodo consequat. Duis autem vel eum iriure dolor in hendrerit in vulputate velit esse molestie consequat, vel illum dolore eu feugiat nulla facilisis at vero eros et accumsan et iusto odio dignissim qui blandit praesent luptatum zzril delenit augue duis dolore te feugait nulla facilisi.</p>
  <span class="btn btn-navy">Read More</span>
</section>

<aside class="quote-form">
  <h2>Get A Quote</h2>
  <form>
    <span class="field">Name</span>
    <span class="field">Email</span>
    <span class="field">Subject</span>
    <span class="field tall">Message</span>
    <span class="submit">SUBMIT</span>
  </form>
</aside>

<section class="audience">
  <div class="half customers">
    <h3>Customers</h3>
    <p>Lorem ipsum dolor sit amet, consectetuer adipiscing elit, sed diam nonummy nibh euismod tincidunt ut laoreet dolore magna aliquam erat volutpat. Ut wisi enim ad minim veniam, quis nostrud exerci tation ullamcorper suscipit lobortis nisl ut aliquip ex ea commodo consequat. Duis autem vel eum iriure dolor in hendrerit in vulputate velit esse molestie consequat.</p>
    <span class="btn btn-navy">Learn More</span>
  </div>
  <div class="half agents">
    <h3>Agents</h3>
    <p>Lorem ipsum dolor sit amet, consectetuer adipiscing elit, sed diam nonummy nibh euismod tincidunt ut laoreet dolore magna aliquam erat volutpat. Ut wisi enim ad minim veniam, quis nostrud exerci tation ullamcorper suscipit lobortis nisl ut aliquip ex ea commodo consequat. Duis autem vel eum iriure dolor in hendrerit in vulputate velit esse molestie consequat.</p>
    <span class="btn btn-red">Learn More</span>
  </div>
</section>
<div class="emblem"></div>

<section class="insurance">
  <div class="heading">
    <h2 class="section-title">Insurance</h2>
    <div class="rule"></div>
  </div>
  <div class="cards">
    <article class="card home">
      <div class="photo" role="img" aria-label="Couple viewing a bright new home interior"></div>
      <div class="body">
        <h4>Homeowner Policy</h4><div class="mini"></div>
        <p>Lorem ipsum dolor sit amet, consectetuer adipiscing elit, sed diam nonummy nibh euismod tincidunt ut laoreet dolore magna aliquam erat volutpat.</p>
        <div class="actions"><span class="btn btn-red">Quote →</span><span class="btn btn-navy">Read More →</span></div>
      </div>
    </article>
    <article class="card tenant">
      <div class="photo" role="img" aria-label="Young couple reviewing a rental agreement together"></div>
      <div class="body">
        <h4>Tenant Policy</h4><div class="mini"></div>
        <p>Lorem ipsum dolor sit amet, consectetuer adipiscing elit, sed diam nonummy nibh euismod tincidunt ut laoreet dolore magna aliquam erat volutpat.</p>
        <div class="actions"><span class="btn btn-red">Quote →</span><span class="btn btn-white">Read More →</span></div>
      </div>
    </article>
    <article class="card flood">
      <div class="photo" role="img" aria-label="Red house damaged and tilted after a flood"></div>
      <div class="body">
        <h4>Flood Policy</h4><div class="mini"></div>
        <p>Lorem ipsum dolor sit amet, consectetuer adipiscing elit, sed diam nonummy nibh euismod tincidunt ut laoreet dolore magna aliquam erat volutpat.</p>
        <div class="actions"><span class="btn btn-red">Quote →</span><span class="btn btn-navy">Read More →</span></div>
      </div>
    </article>
  </div>
</section>

<section class="finder">
  <h2>FIND AN AGENT</h2>
  <div class="bar"></div>
  <p>Lorem ipsum dolor sit amet, consectetuer adipiscing elit, sed diam nonummy nibh euismod tincidunt ut laoreet dolore magna aliquam erat volutpat. Ut wisi enim ad minim veniam, quis nostrud exerci tation ullamcorper suscipit lobortis nisl ut aliquip ex ea commodo consequat.</p>
  <div class="search"><span>Search...</span><span class="btn btn-red">Find An Agent</span></div>
</section>

<section class="claim">
  <h3>Report And Check</h3>
  <div class="big">A Claim</div>
  <p>Login To Report A Claim Or<br>Check Your Claim Status.</p>
  <span class="btn btn-red">Login</span>
</section>
<div class="divider"></div>
<section class="contact">
  <h2 class="section-title">Contact Form</h2>
  <div class="rule"></div>
  <div class="hint">Please fill up bellow form</div>
  <div class="grid">
    <span class="field">Name</span><span class="field">Email</span>
    <span class="field">Phone</span><span class="field">Message</span>
  </div>
  <span class="btn btn-red">Submit</span>
</section>

<footer class="footer">
  <div class="fcol links">
    <h5>Quick Links</h5>
    <ul><li class="current">Home</li><li>About Us</li><li>Insurance</li><li>Agents</li><li>Claims</li><li>Contact Us</li></ul>
  </div>
  <div class="fcol details">
    <h5>Contact Detail</h5>
    <div class="name">Hearthline Insurance</div>
    <p>Lorem ipsum dolor sit amet, consectetur adipiscing elit, sed do eiusmod</p>
    <div class="row"><svg width="14" height="14" viewBox="0 0 24 24"><path fill="#3f63c4" d="M6.6 10.8a15 15 0 0 0 6.6 6.6l2.2-2.2c.3-.3.7-.4 1-.2 1.1.4 2.3.6 3.6.6.6 0 1 .4 1 1V20c0 .6-.4 1-1 1A17 17 0 0 1 3 4c0-.6.4-1 1-1h3.5c.6 0 1 .4 1 1 0 1.3.2 2.5.6 3.6.1.3 0 .7-.2 1z"/></svg>555.014.2290</div>
    <div class="row mail"><svg width="14" height="11" viewBox="0 0 24 18"><rect x="1" y="1" width="22" height="16" fill="none" stroke="#3f63c4" stroke-width="2"/><path d="M1 1l11 9 11-9" fill="none" stroke="#3f63c4" stroke-width="2"/></svg>info@hearthline.com</div>
  </div>
  <div class="fcol news">
    <h5>Join Our Newsletter</h5>
    <p>Subscribe to our Newsletter to get the latest scoop right to your inbox</p>
    <div class="email">Enter Your Email</div>
    <span class="btn btn-red">Subscribe</span>
  </div>
  <div class="fbrand"><div class="sq"></div><span>Hearthline</span></div>
</footer>
<div class="legal">
  <span class="copy">© 2018 Hearthline Insurance. All Rights Reserved.</span>
  <div class="social"><span></span><span></span><span></span></div>
</div>

</body>
</html>
```